Birchline Septic Solutions

Would like to see some single sided ones but would also like to see some double sided with one sided only being the logo. Owners name is Colin Vandro. Phone number is 555-214-0387
Services are pumping, inspections, installs, and repairs

Contact Information for Business Card

555-241-0387 Colin Vandro Greenfield, OH

```html
<!DOCTYPE html>
<html lang="en">
<head>
<meta charset="utf-8">
<title>Birchline Septic Solutions — Business Cards</title>
<link href="https://fonts.googleapis.com/css2?family=Montserrat:wght@400;600;700&display=swap" rel="stylesheet">
<style>
  :root {
    --backdrop: #3b3b3d;
    --card-white: #ffffff;
    --card-black: #0d0d0e;
    --ink: #141414;
    --teal: #1ec2bd;
    --paper-text: #ffffff;
  }
  * { margin: 0; padding: 0; box-sizing: border-box; }
  html, body {
    width: 1200px; height: 1200px; overflow: hidden;
    background: var(--backdrop);
    font-family: "Montserrat", sans-serif;
  }
  .sheet {
    width: 1200px; height: 1200px;
    display: flex; flex-direction: column; align-items: center; justify-content: center;
    gap: 56px;
  }
  .card {
    position: relative;
    width: 880px; height: 503px;
    border-radius: 34px;
    overflow: hidden;
  }
  .card--front { background: var(--card-white); }
  .card--back { background: var(--card-black); }

  .contact {
    position: absolute; left: 92px; top: 168px;
    color: var(--ink);
  }
  .contact__name {
    color: var(--teal); font-weight: 600; font-size: 42px;
    letter-spacing: -1px; line-height: 1;
  }
  .contact__role {
    font-weight: 400; font-size: 27px; letter-spacing: -0.5px;
    line-height: 1; margin-top: 4px;
  }
  .contact__list { list-style: none; margin-top: 20px; }
  .contact__item {
    display: flex; align-items: center; gap: 14px;
    font-size: 22px; line-height: 1; margin-bottom: 10px;
  }
  .contact__icon { width: 24px; height: 24px; flex: none; }

  .brand {
    position: absolute;
    text-align: center;
    font-weight: 700;
    text-transform: uppercase;
    line-height: 1;
  }
  .brand__name { display: block; letter-spacing: 1px; }
  .brand__tag { display: block; letter-spacing: 6px; }
  .card--front .brand {
    color: var(--ink); left: 450px; width: 380px; top: 150px;
  }
  .card--front .brand__name { font-size: 52px; }
  .card--front .brand__tag { font-size: 19px; margin-top: 14px; }
  .card--back .brand {
    color: var(--paper-text); left: 0; width: 880px; top: 188px;
  }
  .card--back .brand__name { font-size: 78px; }
  .card--back .brand__tag { font-size: 27px; margin-top: 18px; letter-spacing: 9px; }

  .band { position: absolute; bottom: 0; }
  .band--teal { left: 0; width: 560px; height: 18px; background: var(--teal); }
  .band--black { left: 572px; right: 0; height: 30px; background: var(--ink); }
</style>
</head>
<body>
<main class="sheet">
  <section class="card card--front" aria-label="Business card front">
    <div class="contact">
      <p class="contact__name">COLIN VANDRO</p>
      <p class="contact__role">OWNER</p>
      <ul class="contact__list">
        <li class="contact__item">
          <svg class="contact__icon" viewBox="0 0 24 24" aria-hidden="true"><path fill="var(--teal)" d="M6.6 10.8a15.2 15.2 0 0 0 6.6 6.6l2.2-2.2c.3-.3.7-.4 1-.2 1.1.4 2.3.6 3.6.6.6 0 1 .4 1 1V20c0 .6-.4 1-1 1A17 17 0 0 1 3 4c0-.6.4-1 1-1h3.5c.6 0 1 .4 1 1 0 1.3.2 2.5.6 3.6.1.3 0 .7-.2 1z"/></svg>
          <span>555-214-0387</span>
        </li>
        <li class="contact__item">
          <svg class="contact__icon" viewBox="0 0 24 24" aria-hidden="true"><rect x="2" y="5" width="20" height="14" rx="1.5" fill="var(--teal)"/><path d="M2.5 6 12 13l9.5-7" fill="none" stroke="#fff" stroke-width="1.6"/></svg>
          <span>colin@birchlineseptic.com</span>
        </li>
        <li class="contact__item">
          <svg class="contact__icon" viewBox="0 0 24 24" aria-hidden="true"><g fill="none" stroke="var(--teal)" stroke-width="1.8"><circle cx="12" cy="12" r="9.5"/><ellipse cx="12" cy="12" rx="4" ry="9.5"/><path d="M2.5 12h19M4 7h16M4 17h16"/></g></svg>
          <span>www.birchlineseptic.com</span>
        </li>
      </ul>
    </div>
    <div class="brand">
      <span class="brand__name">Birchline</span>
      <span class="brand__tag">Septic Solutions</span>
    </div>
    <div class="band band--teal"></div>
    <div class="band band--black"></div>
  </section>

  <section class="card card--back" aria-label="Business card back">
    <div class="brand">
      <span class="brand__name">Birchline</span>
      <span class="brand__tag">Septic Solutions</span>
    </div>
  </section>
</main>
</body>
</html>
```